Pebble Hop - mobile play centre poster designs

Who are we - we are a mobile playground business that specialises in providing entertainment to children in a safe, clean environment either at home or in a function centre. Brief - create 4 different signs to be displayed on our playgrounds. Please find attached 3 photos from our competitors to use as a guide. Corflute sign - size A1 Toddler zone - size A1 Playground rules - size A4 No climbing - size 20cmx8cm sending through photos and documents now.
Colors
Designer to choose colors to be used in the design.
Requirements
Must have
- Colour, be very specific with the rules, pictures

```html
<!DOCTYPE html>
<html lang="en">
<head>
<meta charset="UTF-8">
<title>Pebble Hop – No Climbing Sign</title>
<link rel="stylesheet" href="https://fonts.googleapis.com/css2?family=Anton&display=swap">
<style>
  :root {
    --backdrop: #ececec;
    --sign-yellow: #f3d21c;
    --bamboo-green: #8fc24a;
    --bamboo-light: #c9e08a;
    --panel-cream: #fbf4d2;
    --panel-mint: #e4efd0;
    --panel-sky: #dcefe9;
    --net-grey: #8a8a7e;
    --ban-red: #e8262a;
    --text-red: #ec1c24;
    --text-orange: #f7861f;
  }
  * { box-sizing: border-box; margin: 0; padding: 0; }
  html, body {
    width: 1200px;
    height: 603px;
    overflow: hidden;
    background: var(--backdrop);
  }
  .canvas {
    position: relative;
    width: 1200px;
    height: 603px;
  }
  .sign {
    position: absolute;
    left: 120px;
    top: 112px;
    width: 960px;
    height: 380px;
    background: var(--sign-yellow);
    box-shadow: 0 8px 18px rgba(0,0,0,0.22);
  }
  .bamboo-frame {
    position: absolute;
    inset: 18px 20px;
    background: linear-gradient(180deg, var(--bamboo-light), var(--bamboo-green));
  }
  .jungle-panel {
    position: absolute;
    inset: 34px 36px;
    background:
      radial-gradient(ellipse at 30% 35%, var(--panel-cream) 0%, transparent 60%),
      linear-gradient(180deg, var(--panel-sky) 0%, var(--panel-cream) 55%, var(--panel-mint) 100%);
  }
  .climber-art {
    position: absolute;
    left: 70px;
    top: 92px;
    width: 310px;
    height: 236px;
    background: radial-gradient(ellipse at 50% 50%, #c9c3ad 0%, #ddd8c2 55%, rgba(221,216,194,0) 75%);
  }
  .ban-line {
    position: absolute;
    left: 0;
    top: 0;
    width: 960px;
    height: 380px;
    pointer-events: none;
  }
  .sign-title {
    position: absolute;
    left: 366px;
    top: 118px;
    font-family: "Anton", "Impact", sans-serif;
    font-size: 106px;
    line-height: 1;
    letter-spacing: 0.5px;
    white-space: nowrap;
  }
  .sign-title .no { color: var(--text-red); }
  .sign-title .climbing { color: var(--text-orange); }
</style>
</head>
<body>
  <main class="canvas">
    <section class="sign" aria-label="No climbing sign">
      <div class="bamboo-frame" role="img" aria-label="Bamboo pole frame around the sign"></div>
      <div class="jungle-panel" role="img" aria-label="Soft jungle leaves and clouds background"></div>
      <div class="climber-art" role="img" aria-label="Illustration of a child climbing a rope net"></div>
      <svg class="ban-line" viewBox="0 0 960 380" aria-hidden="true">
        <line x1="98" y1="322" x2="386" y2="42" stroke="var(--ban-red)" stroke-width="4" stroke-linecap="round"/>
      </svg>
      <h1 class="sign-title"><span class="no">NO</span> <span class="climbing">CLIMBING</span></h1>
    </section>
  </main>
</body>
</html>
```